Franchise Power Point

Looking to add a strong design element to a very basic power point presentation about how to find the ideal franchise match. My website is www.tallowbrookventuring.com and www.unitquest/KWendell

```html
<!DOCTYPE html>
<html lang="en">
<head>
<meta charset="utf-8">
<title>UnitQuest – Smart Franchise Decisions Deck</title>
<link href="https://fonts.googleapis.com/css2?family=Lato:wght@300;400;700&display=swap" rel="stylesheet">
<style>
:root{
  --navy:#1b2f4a;
  --navy-deep:#14243a;
  --gold:#f5b71b;
  --page:#f2f2f3;
  --slide:#f8f8f9;
  --card:#fbfbfc;
  --ink:#1d2b40;
  --muted:#6d7480;
}
*{box-sizing:border-box;margin:0;padding:0}
html,body{width:1200px;height:1174px;overflow:hidden;background:var(--page);font-family:'Lato',sans-serif;color:var(--ink)}
.canvas{position:relative;width:1200px;height:1174px}
.slide{position:absolute;width:325px;height:181px;background:var(--slide);box-shadow:0 8px 22px rgba(20,36,58,.12);overflow:hidden}
.c1{left:78px}.c2{left:437px}.c3{left:796px}
.r1{top:68px}.r2{top:282px}.r3{top:496px}.r4{top:710px}.r5{top:924px}
.abs{position:absolute}
.dash{display:block;width:10px;height:1px;background:var(--gold)}
.center{left:0;right:0;text-align:center}
.center .dash{margin:0 auto}
.heading{font-size:11px;font-weight:400;line-height:1.45;color:var(--ink)}
.heading.bold{font-weight:700}
.sub{font-size:4.6px;color:var(--muted);margin-top:3px}
.footer{position:absolute;left:0;right:0;bottom:3px;height:7px;display:flex;align-items:center}
.footer .mark{width:4px;height:7px;background:var(--gold)}
.footer .brand{width:29px;font-size:3.8px;font-weight:700;color:var(--navy);padding-left:2px}
.footer .bar{flex:1;height:7px;background:var(--navy);position:relative;color:#fff;font-size:3.8px;display:flex;align-items:center;justify-content:center}
.footer .pg{position:absolute;right:9px}
.card{position:absolute;background:var(--card);box-shadow:0 3px 9px rgba(20,36,58,.10)}
.card.dark{background:var(--navy);color:#fff}
.tile{display:flex;flex-direction:column;align-items:center;justify-content:center;text-align:center;font-size:3.9px;line-height:1.45;color:var(--muted);padding:0 3px}
.tile.dark{color:#fff}
.tile svg{width:8px;height:8px;margin-bottom:3px}
.tile .dash{width:5px;margin:0 auto 3px}
.photo{position:absolute}
.title-slide{display:flex;flex-direction:column;align-items:center}
.brandmark{font-size:10px;font-weight:700;letter-spacing:.2px;display:flex;align-items:center;gap:3px}
.brandmark i{width:4px;height:4px;background:var(--gold);display:block}
.meta{font-size:4.2px}
.bullets{list-style:none;font-size:4.8px;color:var(--ink)}
.bullets li{display:flex;align-items:center;height:11px}
.bullets li::before{content:"";width:3px;height:3px;border-radius:50%;background:var(--gold);margin-right:4px}
.bio p{font-size:4.2px;line-height:1.6;color:var(--muted);font-weight:300;margin-bottom:4px}
</style>
</head>
<body>
<main class="canvas">

  <!-- 1 cover dark -->
  <section class="slide c1 r1" style="background:var(--navy)">
    <div class="photo" role="img" aria-label="City office towers photo with navy overlay" style="inset:0;background:linear-gradient(115deg,#1a2d4a 0%,#24395a 45%,#3a4d6b 100%)"></div>
    <div class="abs center title-slide" style="top:42px;color:#fff">
      <div class="brandmark">UnitQuest<i></i></div>
      <p class="heading" style="color:#fff;margin-top:12px">Smart Franchise Decisions Using<br>Logic and Intuition</p>
      <p style="font-size:6px;font-weight:700;margin-top:10px">Mr. Owen <span style="color:var(--gold)">Harlow</span></p>
    </div>
    <span class="abs meta" style="left:15px;bottom:11px;color:var(--gold)">May 2024</span>
    <span class="abs meta" style="right:16px;bottom:11px;color:var(--gold)">www.unitquest.com</span>
  </section>

  <!-- 2 cover light -->
  <section class="slide c2 r1" style="background:#fff">
    <div class="abs center title-slide" style="top:42px">
      <div class="brandmark" style="color:var(--navy)">UnitQuest<i></i></div>
      <p class="heading" style="margin-top:12px">Smart Franchise Decisions Using<br>Logic and Intuition</p>
      <p style="font-size:6px;font-weight:700;margin-top:10px">Mr. Owen <span style="color:var(--gold)">Harlow</span></p>
    </div>
    <span class="abs meta" style="left:15px;bottom:11px;color:var(--muted)">May 2024</span>
    <span class="abs meta" style="right:16px;bottom:11px;color:var(--muted)">www.unitquest.com</span>
  </section>

  <!-- 3 quote -->
  <section class="slide c3 r1">
    <div class="card" style="left:40px;top:48px;width:246px;height:85px"></div>
    <div class="abs center" style="top:67px"><span class="dash"></span>
      <p class="heading" style="margin-top:6px">Do not let your Entrepreneurial<br>Dream turn a Technicians Nightmare</p></div>
    <div class="footer"><span class="mark"></span><span class="brand">UnitQuest</span><span class="bar">www.unitquest.com<span class="pg">page &nbsp;|&nbsp; 3</span></span></div>
  </section>

  <!-- 4 statement -->
  <section class="slide c1 r2">
    <div class="card" style="left:40px;top:49px;width:245px;height:84px"></div>
    <div class="abs center" style="top:74px"><span class="dash"></span>
      <p class="heading" style="margin-top:7px">Use the Educated Approach</p></div>
    <div class="footer"><span class="mark"></span><span class="brand">UnitQuest</span><span class="bar">www.unitquest.com<span class="pg">page &nbsp;|&nbsp; 4</span></span></div>
  </section>

  <!-- 5 consultant -->
  <section class="slide c2 r2">
    <div class="card" style="left:31px;top:30px;width:76px;height:120px"></div>
    <div class="abs" style="left:42px;top:37px;width:54px;height:54px;border-radius:50%;border:2.5px solid var(--gold);background:#fff;padding:2px">
      <div role="img" aria-label="Portrait photo of Kara Wendell" style="width:100%;height:100%;border-radius:50%;background:radial-gradient(circle at 50% 40%,#e9c9a8,#c98f5e 70%,#9c6b45)"></div>
    </div>
    <div class="abs" style="left:31px;width:76px;top:96px;text-align:center">
      <p style="font-size:5.8px;font-weight:700;line-height:1.6">Savannah, GA<br>Richmond, VA</p>
      <p style="font-size:3.6px;color:var(--muted);margin-top:6px;line-height:2.2">kwendell@unitquest.com<br>(555) 014-2290</p>
    </div>
    <div class="abs" style="left:129px;top:31px"><span class="dash"></span><p class="heading bold" style="margin-top:6px;font-weight:400">Kara Wendell</p></div>
    <div class="abs bio" style="left:129px;top:61px;width:178px">
      <p>"You decide either to chase your own dreams or to work for someone else who has." Kara lives by this idea. She has built a life where she can do what she loves: helping others find their own balance and fulfillment through ownership.</p>
      <p>Widely known as one of the top franchise consultants in the country, Kara helps you figure out how to do what most people only dream about. She believes that taking control of your career is not selfish, it is necessary. Most people living the dream made their own breaks, did their homework, took risks and kept their eye on the goal.</p>
    </div>
    <div class="footer"><span class="mark"></span><span class="brand">UnitQuest</span><span class="bar">www.unitquest.com<span class="pg">page &nbsp;|&nbsp; 5</span></span></div>
  </section>

  <!-- 6 educated approach -->
  <section class="slide c3 r2">
    <div class="abs" style="left:18px;top:21px"><span class="dash"></span><p class="heading" style="margin-top:6px;font-weight:700;font-size:10.5px">What is the Educated<br>Approach?</p></div>
    <div class="photo" role="img" aria-label="Workshop classroom photo with navy overlay" style="left:166px;top:0;width:159px;height:75px;background:linear-gradient(120deg,#1f3555,#2e4668 60%,#233a5c)"></div>
    <div class="card tile" style="left:18px;top:84px;width:67px;height:57px"><svg viewBox="0 0 10 10" fill="none" stroke="#1b2f4a" stroke-width=".7"><path d="M1 9L5 2l4 7z"/><circle cx="7" cy="2" r="1"/></svg><span class="dash"></span>First Define the<br>Ideal Fit</div>
    <div class="card dark tile" style="left:93px;top:84px;width:67px;height:57px"><svg viewBox="0 0 10 10" fill="none" stroke="#fff" stroke-width=".7"><path d="M1 9h8M2 8V6M4 8V5M6 8V4M8 8V2"/></svg><span class="dash"></span>Focus on options that fit<br>your strengths</div>
    <div class="card tile" style="left:168px;top:84px;width:67px;height:57px"><svg viewBox="0 0 10 10" fill="none" stroke="#1b2f4a" stroke-width=".7"><circle cx="5" cy="5" r="4"/><circle cx="5" cy="5" r="2"/></svg><span class="dash"></span>Focus on options that will meet<br>your lifestyle and financial<br>goals while reducing risk</div>
    <div class="card tile" style="left:243px;top:84px;width:67px;height:57px"><svg viewBox="0 0 10 10" fill="none" stroke="#1b2f4a" stroke-width=".7"><circle cx="5" cy="5" r="1.6"/><path d="M1 3V1h2M7 1h2v2M9 7v2H7M3 9H1V7"/></svg><span class="dash"></span>Put yourself at the<br>center of the search</div>
    <div class="footer"><span class="mark"></span><span class="brand">UnitQuest</span><span class="bar">www.unitquest.com<span class="pg">page &nbsp;|&nbsp; 6</span></span></div>
  </section>

  <!-- 7 key questions -->
  <section class="slide c1 r3">
    <div class="photo" role="img" aria-label="Business meeting photo with dark navy overlay" style="left:0;top:0;width:163px;height:158px;background:linear-gradient(160deg,#1d3350,#182b45 60%,#213a5a)"></div>
    <div class="abs" style="left:19px;top:54px;color:#fff"><span class="dash"></span><p class="heading" style="color:#fff;margin-top:6px;font-size:10.5px;line-height:1.5">Sample Key Questions<br>for the Educated<br>Approach</p></div>
    <ul class="abs bullets" style="left:184px;top:24px">
      <li>Proper investment level</li>
      <li>Skill set and background / personality matching</li>
      <li>Return goals – short, mid and long term</li>
      <li>Employee profile: numbers &amp; backgrounds</li>
      <li>Sales, marketing and advertising</li>
      <li>Concerns around the economy</li>
      <li>Need vs want</li>
      <li>Residual / Repeat / Reoccurring</li>
      <li>Status</li>
      <li>B2B vs B2C</li>
      <li>Full time vs part time vs. managed services</li>
    </ul>
    <div class="footer"><span class="mark"></span><span class="brand">UnitQuest</span><span class="bar">www.unitquest.com<span class="pg">page &nbsp;|&nbsp; 7</span></span></div>
  </section>

  <!-- 8 research method -->
  <section class="slide c2 r3">
    <div class="abs center" style="top:19px"><span class="dash"></span><p class="heading" style="margin-top:5px;font-weight:700;font-size:10.5px">The Research Method</p></div>
    <div class="card tile" style="left:16px;top:58px;width:56px;height:42px"><svg viewBox="0 0 10 10" fill="none" stroke="#1b2f4a" stroke-width=".7"><path d="M2 2h6v6H2zM2 5h6M5 2v6"/></svg>Define Your Ideal<br>Match</div>
    <div class="card dark tile" style="left:76px;top:58px;width:56px;height:42px"><svg viewBox="0 0 10 10" fill="none" stroke="#fff" stroke-width=".7"><circle cx="5" cy="5" r="3.5"/><circle cx="5" cy="5" r="1.3"/></svg>Establish Contact With<br>Target Franchisor</div>
    <div class="card tile" style="left:136px;top:58px;width:56px;height:42px"><svg viewBox="0 0 10 10" fill="none" stroke="#1b2f4a" stroke-width=".7"><path d="M1 5h8M5 1v8"/><circle cx="5" cy="5" r="2.5"/></svg>Work Through Their<br>Standard Process</div>
    <div class="card tile" style="left:196px;top:58px;width:56px;height:42px"><svg viewBox="0 0 10 10" fill="none" stroke="#1b2f4a" stroke-width=".7"><path d="M1 2h8v5H1zM5 7v2M3 9h4"/></svg>Review FDD</div>
    <div class="card tile" style="left:256px;top:58px;width:56px;height:42px"><svg viewBox="0 0 10 10" fill="none" stroke="#1b2f4a" stroke-width=".7"><path d="M2 1h6v8H2zM3.5 3h3M3.5 5h3M3.5 7h2"/></svg>Validate With<br>Franchisees</div>
    <div class="card tile" style="left:16px;top:104px;width:56px;height:42px"><svg viewBox="0 0 10 10" fill="none" stroke="#1b2f4a" stroke-width=".7"><path d="M2 1h6v8H2zM3.5 6l1.5-2 1.5 1 1-2"/></svg>Explore Financing<br>Options</div>
    <div class="card tile" style="left:76px;top:104px;width:56px;height:42px"><svg viewBox="0 0 10 10" fill="none" stroke="#1b2f4a" stroke-width=".7"><circle cx="5" cy="2.5" r="1.3"/><path d="M2 9l1.5-3h3L8 9"/></svg>Discuss Territory</div>
    <div class="card tile" style="left:136px;top:104px;width:56px;height:42px"><svg viewBox="0 0 10 10" fill="none" stroke="#1b2f4a" stroke-width=".7"><path d="M5 9V4M2 2l3 2 3-2M2 5l3 2 3-2"/></svg>Put Together Cash Flow<br>Projections</div>
    <div class="card tile" style="left:196px;top:104px;width:56px;height:42px"><svg viewBox="0 0 10 10" fill="none" stroke="#1b2f4a" stroke-width=".7"><circle cx="3" cy="3" r="1.3"/><circle cx="7" cy="3" r="1.3"/><path d="M1 9V6h4v3M5 9V6h4v3"/></svg>Attend Discovery<br>Day</div>
    <div class="card tile" style="left:256px;top:104px;width:56px;height:42px"><svg viewBox="0 0 10 10" fill="none" stroke="#1b2f4a" stroke-width=".7"><path d="M2 8h3l3-5M6 3h2v2"/><circle cx="2" cy="2.5" r="1.2"/></svg>Make A<br>Decision</div>
    <div class="footer"><span class="mark"></span><span class="brand">UnitQuest</span><span class="bar">www.unitquest.com<span class="pg">page &nbsp;|&nbsp; 8</span></span></div>
  </section>

  <!-- 9 decision making -->
  <section class="slide c3 r3">
    <div class="photo" role="img" aria-label="Photo of a thinking stone statue with a bird" style="left:21px;top:18px;width:110px;height:138px;background:linear-gradient(160deg,#7a4a24,#a98c6e 55%,#5a3a22)"></div>
    <div class="abs" style="left:145px;top:63px"><span class="dash"></span><p class="heading" style="margin-top:5px;font-weight:700">Decision Making</p><p class="sub">Right Brain vs. Left Brain</p></div>
    <div class="footer"><span class="mark"></span><span class="brand">UnitQuest</span><span class="bar">www.unitquest.com<span class="pg">page &nbsp;|&nbsp; 9</span></span></div>
  </section>

  <!-- 10 fear -->
  <section class="slide c1 r4">
    <div class="photo" role="img" aria-label="Photo of ancient remains in earth tones" style="left:20px;top:18px;width:110px;height:138px;background:linear-gradient(150deg,#5a2a12,#b0602a 50%,#6a3014)"></div>
    <div class="abs" style="left:145px;top:63px"><span class="dash"></span><p class="heading" style="margin-top:5px;font-weight:700">Fear</p><p class="sub">The human spirit resist's change</p></div>
    <div class="footer"><span class="mark"></span><span class="brand">UnitQuest</span><span class="bar">www.unitquest.com<span class="pg">page &nbsp;|&nbsp; 10</span></span></div>
  </section>

  <!-- 11 booth -->
  <section class="slide c2 r4">
    <div class="photo" role="img" aria-label="Photo of a dam and river gorge" style="left:20px;top:18px;width:110px;height:138px;background:linear-gradient(180deg,#9aa690 0%,#66705a 35%,#2f6a6e 65%,#b9bcb5 100%)"></div>
    <div class="abs" style="left:145px;top:54px"><span class="dash"></span><p class="heading" style="margin-top:5px;font-weight:700;font-size:10.5px;line-height:1.5">Stop by my Booth, Ask Me<br>ANY Question and Receive a<br>Free Copy of The Franchise<br>Field Guide</p></div>
    <div class="footer"><span class="mark"></span><span class="brand">UnitQuest</span><span class="bar">www.unitquest.com<span class="pg">page &nbsp;|&nbsp; 11</span></span></div>
  </section>

  <!-- 12 dam or river -->
  <section class="slide c3 r4">
    <div class="photo" role="img" aria-label="Book cover illustration with an apple" style="left:21px;top:18px;width:110px;height:138px;background:linear-gradient(180deg,#1f4a6a 0%,#1f4a6a 18%,#f4f4f2 18%,#f4f4f2 90%,#1f4a6a 90%)"></div>
    <div class="abs" style="left:145px;top:58px"><span class="dash"></span><p class="heading" style="margin-top:5px;font-weight:700;font-size:10.5px;line-height:1.5">Are you the dam or<br>are you the River?</p></div>
    <div class="footer"><span class="mark"></span><span class="brand">UnitQuest</span><span class="bar">www.unitquest.com<span class="pg">page &nbsp;|&nbsp; 12</span></span></div>
  </section>

  <!-- 13 top dozen A -->
  <section class="slide c1 r5">
    <div class="abs center" style="top:19px"><span class="dash"></span><p class="heading" style="margin-top:5px;font-weight:700;font-size:10.5px">My Top Dozen for 2024</p></div>
    <div class="card tile" style="left:26px;top:52px;width:67px;height:48px"><svg viewBox="0 0 10 10" fill="none" stroke="#1b2f4a" stroke-width=".7"><circle cx="3" cy="3" r="1.3"/><circle cx="7" cy="3" r="1.3"/><path d="M1 9V6h4v3M5 9V6h4v3"/></svg><span class="dash"></span>Pet Options</div>
    <div class="card tile" style="left:127px;top:52px;width:67px;height:48px"><svg viewBox="0 0 10 10" fill="none" stroke="#1b2f4a" stroke-width=".7"><path d="M1 9L5 2l4 7z"/><circle cx="7" cy="2" r="1"/></svg><span class="dash"></span>Real Estate Options</div>
    <div class="card tile" style="left:226px;top:52px;width:67px;height:48px"><svg viewBox="0 0 10 10" fill="none" stroke="#1b2f4a" stroke-width=".7"><circle cx="5" cy="4" r="3"/><path d="M4 7v2h2V7"/></svg><span class="dash"></span>Mental Health</div>
    <div class="card tile" style="left:26px;top:110px;width:67px;height:48px"><svg viewBox="0 0 10 10" fill="none" stroke="#1b2f4a" stroke-width=".7"><circle cx="5" cy="2.5" r="1.3"/><path d="M2 9l1.5-3h3L8 9"/></svg><span class="dash"></span>Seniors and<br>Children</div>
    <div class="card tile" style="left:127px;top:110px;width:67px;height:48px"><svg viewBox="0 0 10 10" fill="none" stroke="#1b2f4a" stroke-width=".7"><path d="M5 9V4M2 2l3 2 3-2M2 5l3 2 3-2"/></svg><span class="dash"></span>Health and<br>Wellness</div>
    <div class="card tile" style="left:226px;top:110px;width:67px;height:48px"><svg viewBox="0 0 10 10" fill="none" stroke="#1b2f4a" stroke-width=".7"><path d="M1 2h8v7H1zM3 7l2-3 2 3"/></svg><span class="dash"></span>Owner Operator to Area<br>Developer</div>
    <div class="footer"><span class="mark"></span><span class="brand">UnitQuest</span><span class="bar">www.unitquest.com<span class="pg">page &nbsp;|&nbsp; 13</span></span></div>
  </section>

  <!-- 14 top dozen B -->
  <section class="slide c2 r5">
    <div class="abs center" style="top:19px"><span class="dash"></span><p class="heading" style="margin-top:5px;font-weight:700;font-size:10.5px">My Top Dozen for 2024</p></div>
    <div class="card tile" style="left:26px;top:52px;width:67px;height:48px"><svg viewBox="0 0 10 10" fill="none" stroke="#1b2f4a" stroke-width=".7"><circle cx="5" cy="5" r="3.5"/><path d="M5 1.5v7M1.5 5h7"/></svg><span class="dash"></span>Emergency<br>Restoration</div>
    <div class="card tile" style="left:127px;top:52px;width:67px;height:48px"><svg viewBox="0 0 10 10" fill="none" stroke="#1b2f4a" stroke-width=".7"><path d="M2 1h6v8H2z"/><circle cx="5" cy="5" r="1.5"/></svg><span class="dash"></span>Low Status Options</div>
    <div class="card tile" style="left:226px;top:52px;width:67px;height:48px"><svg viewBox="0 0 10 10" fill="none" stroke="#1b2f4a" stroke-width=".7"><path d="M4 1h2v3H4zM3 4h4v5H3z"/></svg><span class="dash"></span>Home Services</div>
    <div class="card tile" style="left:26px;top:110px;width:67px;height:48px"><svg viewBox="0 0 10 10" fill="none" stroke="#1b2f4a" stroke-width=".7"><path d="M1 4h8v3H1zM2.5 4v3M5 4v3M7.5 4v3"/></svg><span class="dash"></span>Rental Options</div>
    <div class="card tile" style="left:127px;top:110px;width:67px;height:48px"><svg viewBox="0 0 10 10" fill="none" stroke="#1b2f4a" stroke-width=".7"><path d="M2 2h6v7H2zM5 2v7"/></svg><span class="dash"></span>Clothing Recycling</div>
    <div class="card tile" style="left:226px;top:110px;width:67px;height:48px"><svg viewBox="0 0 10 10" fill="none" stroke="#1b2f4a" stroke-width=".7"><path d="M1 3h6v4H1zM7 4h2v3H7"/><circle cx="3" cy="8" r="1"/><circle cx="7" cy="8" r="1"/></svg><span class="dash"></span>Food Trucks / Restaurants</div>
    <div class="footer"><span class="mark"></span><span class="brand">UnitQuest</span><span class="bar">www.unitquest.com<span class="pg">page &nbsp;|&nbsp; 14</span></span></div>
  </section>

  <!-- 15 courtesy -->
  <section class="slide c3 r5">
    <div class="abs center" style="top:19px"><span class="dash"></span><p class="heading" style="margin-top:5px;font-weight:700;font-size:10.5px">Courtesy of:</p></div>
    <div class="card" style="left:97px;top:70px;width:131px;height:91px"></div>
    <div class="abs" role="img" aria-label="Portrait photo of Kara Wendell" style="left:146px;top:52px;width:32px;height:32px;border-radius:50%;border:1.5px solid #fff;background:radial-gradient(circle at 50% 40%,#e9c9a8,#c98f5e 70%,#9c6b45)"></div>
    <div class="abs center" style="top:90px">
      <p style="font-size:5px;font-weight:700;line-height:1.9">Kara Wendell<br>(555) 014-2290</p>
      <p style="font-size:4px;color:var(--muted);margin-top:4px;line-height:2">kwendell@unitquest.com<br>http://www.tallowbrookventuring.com</p>
    </div>
    <div class="footer"><span class="mark"></span><span class="brand">UnitQuest</span><span class="bar">www.unitquest.com<span class="pg">page &nbsp;|&nbsp; 15</span></span></div>
  </section>

</main>
</body>
</html>
```